TLK Electricial Contracting Services

Hi guys, after a design for my small electrical company, have logo design files to be incorporated into the layout, the basic concept is electrical contracting services for residential, commercial, industrial & data services, image is clean clear and strong,

Card format is to have a nice clean logo on front,with maybe the Residential – commercial – industrial - data, followed with licensed & insured, followed by contact details on backside of the card.

Target Market(s)

Residential, commercial, industrial sectors.

Industry/Entity Type

Electrical

Contact Information for Business Card

TLK logo,
Residential – commercial – industrial - data
REC: 61307
Email: tlk@vornamail.net.au
Phone: 0487 352 019

Requirements
Must have
• Clean & strong design.
Nice to have
• If possible, I would like the logo colours inverted so the text is orange and the background is black on the front of the card, then the backside of the card be the reverse colour
Should not have
• No Sparks, lightning bolts,

```html
<!DOCTYPE html>
<html lang="en">
<head>
<meta charset="utf-8">
<title>TLK Electricial Contracting Services – Business Card</title>
<link href="https://fonts.googleapis.com/css2?family=Lato:wght@400;700;900&display=swap" rel="stylesheet">
<style>
  :root {
    --backdrop: #3b3b3b;
    --card-black: #000000;
    --brand-orange: #f4822a;
    --ink-black: #0a0a0a;
  }
  * { margin: 0; padding: 0; box-sizing: border-box; }
  html, body {
    width: 1200px;
    height: 900px;
    overflow: hidden;
    background: var(--backdrop);
    font-family: "Lato", Arial, sans-serif;
  }
  .stage { position: relative; width: 1200px; height: 900px; }
  .card {
    position: absolute;
    top: 205px;
    width: 294px;
    height: 483px;
    border-radius: 12px;
    text-align: center;
  }
  .card--front { left: 287px; background: var(--card-black); color: var(--brand-orange); }
  .card--back { left: 645px; background: var(--brand-orange); color: var(--ink-black); }

  .brand { position: absolute; left: 0; right: 0; }
  .card--front .brand { top: 128px; }
  .card--back .brand { top: 146px; }
  .brand-name {
    font-weight: 900;
    font-size: 66px;
    line-height: 1;
    letter-spacing: -1px;
  }
  .brand-tagline {
    margin-top: 4px;
    font-weight: 700;
    font-size: 14px;
  }

  .services {
    position: absolute;
    top: 250px; left: 0; right: 0;
    list-style: none;
    font-size: 14px;
    line-height: 18px;
    text-transform: uppercase;
  }
  .licence {
    position: absolute;
    top: 339px; left: 0; right: 0;
    font-size: 14px;
  }

  .contact {
    position: absolute;
    top: 257px; left: 0; right: 0;
    list-style: none;
    font-size: 15px;
    line-height: 19px;
  }
  .contact li { display: flex; justify-content: center; align-items: center; gap: 6px; }
  .contact svg { width: 11px; height: 11px; fill: var(--ink-black); }
</style>
</head>
<body>
<main class="stage">
  <section class="card card--front" aria-label="Card front">
    <div class="brand">
      <p class="brand-name">TLK</p>
      <p class="brand-tagline">Tara Lee Kent Electrical</p>
    </div>
    <ul class="services">
      <li>Residential</li>
      <li>Commercial</li>
      <li>Industrial</li>
      <li>Data</li>
    </ul>
    <p class="licence">REC: 61307</p>
  </section>

  <section class="card card--back" aria-label="Card back">
    <div class="brand">
      <p class="brand-name">TLK</p>
      <p class="brand-tagline">Tara Lee Kent Electrical</p>
    </div>
    <ul class="contact">
      <li>
        <svg viewBox="0 0 12 12" aria-hidden="true"><path d="M1 4 Q6 0 11 4 L9 5.5 L8 4 L4 4 L3 5.5 Z M3 6 L9 6 L10.5 11 L1.5 11 Z"/></svg>
        <span>0487 352 019</span>
      </li>
      <li>
        <svg viewBox="0 0 12 12" aria-hidden="true"><path d="M1 3 H11 V10 H1 Z" /><path d="M1 3 L6 7 L11 3" stroke="#f4822a" stroke-width="1" fill="none"/></svg>
        <span>tlk@vornamail.net.au</span>
      </li>
    </ul>
  </section>
</main>
</body>
</html>
```